Australian Trucking Company Requires Professional Looking Stationary

We require a professional looking stationary design that incorporates our newly designed logo.

Our business, called "Brell Haulage Contracting", provides contracting work, transport and logistics to business in Western Australia particularly with links to the mining sector.

We are a small business looking to expand and our new logo and our new stationary will help develop our brand image in our market place.

Target Market(s)

Businesses and Corporation with links to the Mining Sector

Industry/Entity Type

Small Business

Requirements
Must have
• The letterhead must have the following details:
The new logo

Text saying: "Brell Holdings Pty Ltd (ACN 582 316 907) ATF The Brell Discretionary Trust T/AS"
"ABN 71 834 209 553"
Address "P.O Box 817 Wattlegrove WA, 6958"
Phone: 08 9352 7140
Email: brellhaul@mailbox-example.com.au

The text on the letterhead should be editable as the details are likely to change in the near future. Provision should be made for a website address all though one isn't available at the moment.

The styling, layout and font text is entirely up to the designer.

```html
<!DOCTYPE html>
<html lang="en">
<head>
<meta charset="utf-8">
<title>Brell Haulage Contracting – Business Card</title>
<link href="https://fonts.googleapis.com/css2?family=Arimo:wght@400;700&display=swap" rel="stylesheet">
<style>
  :root {
    --bg: #e8e5e1;
    --card: #ffffff;
    --brand-red: #a3161c;
    --text-grey: #444444;
    --muted-grey: #7a7a7a;
    --mark-grey: #555555;
  }
  * { margin: 0; padding: 0; box-sizing: border-box; }
  html, body { width: 1200px; height: 1200px; overflow: hidden; }
  body {
    background: var(--bg);
    font-family: "Arimo", Arial, sans-serif;
    position: relative;
  }
  .card {
    position: absolute;
    width: 840px;
    height: 480px;
    background: var(--card);
    box-shadow: 0 2px 8px rgba(0,0,0,0.12);
  }
  .card--front { left: 84px; top: 78px; }
  .card--back { left: 284px; top: 650px; }

  .brand-square {
    position: absolute;
    left: 110px; top: 70px;
    width: 120px; height: 120px;
    background: var(--mark-grey);
  }
  .brand-name {
    position: absolute;
    left: 304px; top: 58px;
    color: var(--brand-red);
    font-weight: 700;
    font-size: 46px;
    line-height: 52px;
    text-transform: uppercase;
    letter-spacing: 1px;
  }

  .person {
    position: absolute;
    right: 580px; top: 290px;
    text-align: right;
    color: var(--brand-red);
  }
  .person__name { font-size: 31px; font-weight: 700; line-height: 36px; }
  .person__title { font-size: 24px; letter-spacing: 2px; line-height: 40px; }

  .contacts {
    position: absolute;
    right: 44px; top: 292px;
    list-style: none;
    text-align: right;
    color: var(--text-grey);
    font-size: 22px;
    line-height: 33.5px;
  }
  .contacts li { display: flex; justify-content: flex-end; align-items: center; gap: 8px; }
  .contacts svg { width: 17px; height: 17px; fill: var(--brand-red); flex: none; }

  .back-brand {
    position: absolute;
    left: 0; right: 0; top: 80px;
    text-align: center;
    color: var(--mark-grey);
    font-weight: 700;
    font-size: 54px;
    line-height: 62px;
    text-transform: uppercase;
    letter-spacing: 2px;
  }
  .entity {
    position: absolute;
    left: 0; right: 0; top: 360px;
    text-align: center;
    color: var(--muted-grey);
    font-size: 22px;
    line-height: 30px;
  }
  .web {
    position: absolute;
    left: 0; right: 0; top: 428px;
    text-align: center;
    color: #333333;
    font-size: 30px;
    letter-spacing: 2px;
  }
  .web strong { color: var(--brand-red); font-weight: 700; }
</style>
</head>
<body>
  <section class="card card--front">
    <div class="brand-square"></div>
    <div class="brand-name">Brell<br>Haulage<br>Contracting</div>

    <div class="person">
      <p class="person__name">Your Name</p>
      <p class="person__title">Title</p>
    </div>

    <ul class="contacts">
      <li>
        <svg viewBox="0 0 24 24" aria-hidden="true"><path d="M6.6 10.8a15.1 15.1 0 0 0 6.6 6.6l2.2-2.2a1 1 0 0 1 1-.25 11.4 11.4 0 0 0 3.6.57 1 1 0 0 1 1 1V20a1 1 0 0 1-1 1A17 17 0 0 1 3 4a1 1 0 0 1 1-1h3.5a1 1 0 0 1 1 1c0 1.25.2 2.45.57 3.57a1 1 0 0 1-.25 1z"/></svg>
        08 9352 7140
      </li>
      <li>
        <svg viewBox="0 0 24 24" aria-hidden="true"><path d="M2 5h20v14H2z M2 5l10 7 10-7" fill="var(--brand-red)"/><path d="M2 6l10 7 10-7" fill="none" stroke="#fff" stroke-width="1.5"/></svg>
        brellhaul@mailbox-example.com.au
      </li>
      <li>
        <svg viewBox="0 0 24 24" aria-hidden="true"><circle cx="12" cy="12" r="9" fill="none" stroke="var(--brand-red)" stroke-width="2"/><path d="M3 12h18M12 3c3 3 3 15 0 18M12 3c-3 3-3 15 0 18" fill="none" stroke="var(--brand-red)" stroke-width="1.5"/></svg>
        www.brellhaulage.com
      </li>
      <li>
        <svg viewBox="0 0 24 24" aria-hidden="true"><path d="M12 3l10 9h-3v9h-5v-6h-4v6H5v-9H2z"/></svg>
        P.O Box 817 Wattlegrove WA, 6958
      </li>
    </ul>
  </section>

  <section class="card card--back">
    <div class="back-brand">Brell<br>Haulage<br>Contracting</div>
    <p class="entity">Brell Holdings Pty Ltd (ACN 582 316 907)<br>ATF The Brell Discretionary Trust T/AS</p>
    <p class="web">www.<strong>brellhaulage</strong>.com</p>
  </section>
</body>
</html>
```